business card for a massage therapy practice named 'Cedar and Willow Massage Studio'

I really need a trendy, yet easy on the eyes business card to complement my logo. Ideally with some gold or rose gold foil work.

My uploaded file of the logo I have in horizontal but I have a vertical version as well. Another color that is used in the website is a blush pink here and there. I'd like to see some trendy tropical leaves in the design.

```html
<!DOCTYPE html>
<html lang="en">
<head>
<meta charset="utf-8">
<title>Cedar and Willow Massage Studio – Business Card</title>
<link rel="stylesheet" href="https://fonts.googleapis.com/css2?family=Questrial&family=Amatic+SC:wght@700&display=swap">
<style>
  :root {
    --backdrop: #ebebeb;
    --card: #fbfbfb;
    --gold: #9a8452;
    --ink: #3a3a3a;
    --leaf: #6ea043;
    --leaf-soft: #9cc47a;
    --mint: #7fd1b8;
    --pattern-green: #4d9a6a;
  }
  * { margin: 0; padding: 0; box-sizing: border-box; }
  html, body {
    width: 1200px; height: 1200px; overflow: hidden;
    background: var(--backdrop);
    font-family: "Questrial", sans-serif;
  }
  .stage {
    position: relative; width: 1200px; height: 1200px;
    display: flex; justify-content: center; align-items: center; gap: 60px;
  }
  .card {
    position: relative; width: 420px; height: 720px;
    background: var(--card);
    box-shadow: 0 10px 30px rgba(0,0,0,0.12);
    overflow: hidden;
  }

  /* Back side */
  .card-back .pattern {
    position: absolute; inset: 0;
    background:
      radial-gradient(circle at 30% 25%, rgba(154,132,82,0.28), transparent 45%),
      radial-gradient(circle at 70% 75%, rgba(77,154,106,0.22), transparent 45%),
      linear-gradient(160deg, #f3efe4, #e9efe7);
  }
  .card-back .logo-frame {
    position: absolute; left: 50%; top: 50%;
    width: 280px; height: 200px;
    transform: translate(-50%, -50%);
    background: linear-gradient(135deg, #ffffff, #ececec);
    border: 3px solid var(--gold);
    display: flex; align-items: center; justify-content: center; gap: 12px;
    padding: 0 20px;
  }

  /* Shared wordmark */
  .wordmark {
    display: flex; align-items: center; gap: 12px;
  }
  .wordmark-dot {
    flex: none; width: 14px; height: 14px; border-radius: 50%;
    background: var(--gold);
  }
  .wordmark-name {
    color: var(--gold); font-family: "Questrial", sans-serif;
    font-size: 22px; line-height: 1.25; letter-spacing: 0.04em;
    text-transform: uppercase;
  }

  /* Front side */
  .card-front .foliage {
    position: absolute; top: 0; right: 0;
    width: 270px; height: 230px;
    background: radial-gradient(ellipse at 75% 20%, var(--leaf) 0%, var(--leaf-soft) 45%, rgba(156,196,122,0) 72%);
  }
  .card-front .wordmark {
    position: absolute; left: 50px; top: 330px; right: 40px;
  }
  .card-front .wordmark-name { font-size: 28px; }
  .person {
    position: absolute; left: 50px; top: 500px;
  }
  .person-name {
    font-family: "Amatic SC", sans-serif; font-weight: 700;
    font-size: 44px; color: var(--gold); letter-spacing: 0.03em; line-height: 1;
  }
  .person-role {
    font-size: 19px; color: var(--ink); letter-spacing: 0.08em; margin: 4px 0 0 14px;
  }
  .contact {
    position: absolute; left: 50px; top: 610px;
    list-style: none; font-size: 18px; line-height: 1.6; color: var(--ink);
  }
  .contact-label { color: var(--gold); }
</style>
</head>
<body>
<main class="stage">
  <section class="card card-back">
    <div class="pattern" role="img" aria-label="Repeating pattern of gold pineapples with green leaves"></div>
    <div class="logo-frame">
      <div class="wordmark">
        <span class="wordmark-dot"></span>
        <span class="wordmark-name">Cedar and Willow Massage Studio</span>
      </div>
    </div>
  </section>

  <section class="card card-front">
    <div class="foliage" role="img" aria-label="Illustrated green tropical palm leaves in the top corner"></div>
    <div class="wordmark">
      <span class="wordmark-dot"></span>
      <span class="wordmark-name">Cedar and Willow Massage Studio</span>
    </div>
    <div class="person">
      <p class="person-name">MARA ELLIS</p>
      <p class="person-role">Artist</p>
    </div>
    <ul class="contact">
      <li><span class="contact-label">Phone:</span> +123 456 789 0</li>
      <li><span class="contact-label">Email:</span> lorem@ipsum.com</li>
      <li><span class="contact-label">Web:</span> www.yourwebsite.com</li>
    </ul>
  </section>
</main>
</body>
</html>
```